Tall fern bicycle rental

would like to have a bicycle rental website that has the ability to have a calender and be able to sign a liability waiver and pay all on line, We rent fat tire vorn bicycles

```html
<!DOCTYPE html>
<html lang="en">
<head>
<meta charset="utf-8">
<title>Tall Fern Bicycle Rental</title>
<link href="https://fonts.googleapis.com/css2?family=Titillium+Web:wght@400;600;700&family=Open+Sans:wght@400;600;700&display=swap" rel="stylesheet">
<style>
:root{
  --blue:#1f6fc1;
  --blue-bright:#2c8ad6;
  --navy:#1b4f86;
  --navy-deep:#173f6c;
  --footer:#1e4b7e;
  --footer-bar:#1a4170;
  --ink:#333;
  --muted:#555;
  --paper:#f2f2f2;
  --white:#fff;
}
*{box-sizing:border-box;margin:0;padding:0}
html,body{width:1200px;height:4005px;overflow:hidden}
body{position:relative;background:var(--paper);font-family:"Open Sans",Arial,sans-serif;color:var(--ink)}
.abs{position:absolute}
.heading{font-family:"Titillium Web",Arial,sans-serif;font-weight:700;text-transform:uppercase;line-height:1.1}
.btn{position:absolute;display:flex;align-items:center;justify-content:center;border-radius:30px;font-family:"Titillium Web",Arial,sans-serif;font-weight:700;font-size:19px;text-transform:uppercase}
.btn-solid{background:var(--blue-bright);color:var(--white)}
.btn-outline{border:2px solid var(--blue);color:var(--blue);background:transparent}
.btn-white{background:var(--white);color:var(--blue)}

/* header */
.site-header{position:absolute;left:0;top:0;width:1200px;height:103px;background:var(--white);z-index:5}
.brand{position:absolute;left:85px;top:26px;display:flex;align-items:center;gap:12px}
.brand-dot{width:50px;height:50px;border-radius:50%;background:var(--blue)}
.brand-name{font-family:"Titillium Web",Arial,sans-serif;font-weight:700;font-size:34px;color:var(--blue);text-transform:uppercase;letter-spacing:1px}
.main-nav{position:absolute;top:38px;left:0;width:1200px;font-family:"Titillium Web",Arial,sans-serif;font-size:17px;color:#222}
.main-nav span{position:absolute;text-transform:uppercase}
.main-nav .active{color:var(--blue-bright)}

/* hero */
.hero-photo{left:0;top:103px;width:1200px;height:690px;background:linear-gradient(180deg,#5c93c9 0%,#8fb6d9 38%,#8a8a86 60%,#5e5850 80%,#3f3a35 100%)}
.hero-edge{left:0;top:690px;width:1200px;height:110px}
.hero-title{left:40px;top:288px;width:510px;text-align:center;color:var(--white);font-size:47px}
.hero-text{left:80px;top:407px;width:430px;text-align:center;color:#e8eef5;font-size:15px;line-height:1.9}
.carousel-dots{left:1135px;top:370px;width:14px}
.carousel-dots i{display:block;width:13px;height:13px;border-radius:50%;background:var(--white);margin-bottom:10px}
.carousel-dots i.current{background:transparent;border:2px solid var(--white)}

/* about */
.about-photo{left:151px;top:822px;width:398px;height:398px;border-radius:50%;background:radial-gradient(circle at 45% 40%,#d9e1ea 0%,#8ca3bd 45%,#2d4f7d 100%)}
.about-bike{left:479px;top:1180px;width:236px;height:140px;border-radius:50%;background:radial-gradient(ellipse,#3d4a5a 0%,rgba(61,74,90,.35) 55%,rgba(61,74,90,0) 72%);z-index:3}
.about-copy{left:595px;top:814px;width:500px;text-align:center}
.eyebrow{font-family:"Titillium Web",Arial,sans-serif;font-weight:700;font-size:31px;color:var(--blue-bright);text-transform:uppercase;line-height:1.2}
.about-copy h2{font-size:44px;color:var(--navy)}
.about-copy p{font-size:16px;line-height:1.65;color:var(--muted);margin-top:20px}
.about-copy p + p{margin-top:16px}

/* booking */
.booking-photo{left:0;top:1190px;width:1200px;height:683px;background:linear-gradient(120deg,#1d5fa8 0%,#2c82cc 45%,#3b95db 70%,#2a79c4 100%)}
.booking-curve{left:0;top:1188px;width:1200px;height:140px}
.booking-title{left:148px;top:1452px;font-size:38px;color:var(--white)}
.booking-text{left:148px;top:1510px;width:440px;color:#eef4fb;font-size:15.5px;line-height:1.5}
.booking-text p + p{margin-top:10px}
.calendar{left:668px;top:1417px;width:407px;border-collapse:collapse;font-family:"Titillium Web",Arial,sans-serif}
.calendar-head{height:47px;background:var(--white);display:flex;align-items:center;justify-content:center;gap:48px;color:var(--blue);font-size:22px;font-weight:600}
.calendar-head b{font-weight:400;font-size:26px;color:#555}
.calendar table{width:100%;border-collapse:collapse;background:var(--navy);color:var(--white);table-layout:fixed}
.calendar th{height:44px;background:#2f78bf;font-size:14px;font-weight:600}
.calendar td{height:48px;text-align:center;font-size:21px;font-weight:600;border:1px solid #2f6aa5}

/* how it works */
.section-title{width:1200px;left:0;text-align:center;color:var(--navy);font-size:35px}
.steps{left:0;top:2000px;width:1200px;height:200px}
.step-label{position:absolute;width:220px;text-align:center;font-family:"Open Sans",Arial,sans-serif;font-weight:700;font-size:17px;line-height:1.3;color:#222;text-transform:uppercase}
.people-photo{left:0;top:2150px;width:1200px;height:430px;background:linear-gradient(180deg,rgba(242,242,242,0) 0%,#b9cbd9 20%,#7e98b4 50%,#5d7c52 78%,#3e5a38 100%)}
.people-edge{left:0;top:2490px;width:1200px;height:95px}

/* testimonials */
.testimonial-img{height:202px;width:302px;top:2668px}
.testimonial-card{position:absolute;top:2831px;width:265px;height:176px;background:var(--white);box-shadow:0 3px 10px rgba(0,0,0,.15);text-align:center;padding:26px 20px 0;font-size:13.5px;line-height:1.7;color:var(--muted)}
.testimonial-card strong{display:block;margin-top:10px;color:#333;font-weight:700}
.testimonial-card.featured{background:linear-gradient(180deg,var(--navy) 0%,#2a82cf 100%);color:#e8f0f9}
.testimonial-card.featured strong{color:var(--white)}

/* call to action */
.cta-photo{left:0;top:3108px;width:1200px;height:560px;background:linear-gradient(180deg,#2a74c4 0%,#6ea6dc 40%,#a9c9e6 62%,#6e8a9a 78%,#2f5879 100%)}
.cta-title{left:152px;top:3226px;font-size:40px;color:var(--blue-bright)}
.cta-text{left:152px;top:3326px;width:460px;font-size:15.5px;line-height:1.55;color:#1d2a38}
.footer-edge{left:0;top:3580px;width:1200px;height:70px}

/* footer */
.site-footer{left:0;top:3644px;width:1200px;height:296px;background:var(--footer)}
.footer-mark{left:155px;top:3696px;width:168px;height:168px;border-radius:50%;background:var(--white);display:flex;align-items:center;justify-content:center;font-family:"Titillium Web",Arial,sans-serif;font-weight:700;font-size:28px;color:var(--blue);text-transform:uppercase;text-align:center;line-height:1.05}
.footer-col{top:3706px;color:var(--white)}
.footer-col h4{font-family:"Titillium Web",Arial,sans-serif;font-weight:700;font-size:19px;text-transform:uppercase;margin-bottom:14px}
.footer-col li{list-style:none;font-size:14px;line-height:27px;color:#dfe8f3}
.footer-col li.indent{padding-left:4px}
.social{display:flex;gap:6px}
.social i{width:30px;height:30px;border-radius:50%;border:1.5px solid var(--white)}
.footer-bar{left:0;top:3940px;width:1200px;height:65px;background:var(--footer-bar);color:#d7e2ef;font-size:12px;text-align:center;line-height:65px}
</style>
</head>
<body>

<header class="site-header">
  <div class="brand"><span class="brand-dot"></span><span class="brand-name">Tall Fern</span></div>
  <nav class="main-nav">
    <span class="active" style="left:432px">Home</span>
    <span style="left:524px">About Us</span>
    <span style="left:646px">Bike Rent</span>
    <span style="left:769px">Calendar</span>
    <span style="left:897px">Book Now</span>
    <span style="left:1026px">Contact</span>
  </nav>
</header>

<section class="hero">
  <div class="abs hero-photo" role="img" aria-label="Rider jumping a fat tire bicycle over a rocky lakeshore with hills behind"></div>
  <svg class="abs hero-edge" viewBox="0 0 1200 110" preserveAspectRatio="none" aria-hidden="true">
    <path d="M0 70 Q150 20 300 55 T600 40 T900 55 T1200 30 V110 H0 Z" fill="var(--paper)"/>
  </svg>
  <h1 class="abs heading hero-title">Rent Bicycle for<br>Your Journey</h1>
  <p class="abs hero-text">Lorem ipsum dolor sit amet consectetuer adipiscing elit Nam cursus Morbi ut mi Nullam enim</p>
  <a class="btn btn-solid" style="left:197px;top:477px;width:187px;height:52px">Book Now</a>
  <div class="abs carousel-dots"><i class="current"></i><i></i><i></i><i></i></div>
</section>

<section class="about">
  <div class="abs about-photo" role="img" aria-label="Cyclist riding through a snowy forest, framed in a circle"></div>
  <div class="abs about-bike" role="img" aria-label="Black fat tire bicycle"></div>
  <div class="abs about-copy">
    <div class="eyebrow">Welcome</div>
    <h2 class="heading">About Tall Fern</h2>
    <p>Arna Sed porta Suspendisse quam leo molestie sed luctus quis feugiat in pede Fusce tellus Sed metus augue convall</p>
    <p>consequat nec porta vel lectus Nulla sit amet diam Duis non nunc Nulla rhoncus dictum metus Curabitur tristique mi condimentum orci Phasellus pellentesque aliquam</p>
  </div>
  <a class="btn btn-outline" style="left:743px;top:1091px;width:194px;height:59px">Learn More</a>
</section>

<section class="booking">
  <div class="abs booking-photo" role="img" aria-label="Rider on a fat tire bicycle on a winter trail, tinted blue"></div>
  <svg class="abs booking-curve" viewBox="0 0 1200 140" preserveAspectRatio="none" aria-hidden="true">
    <path d="M0 0 H1200 V9 Q600 255 0 9 Z" fill="var(--paper)"/>
  </svg>
  <h2 class="abs heading booking-title">Book Bicycle Now</h2>
  <div class="abs booking-text">
    <p>Arna Sed porta Suspendisse quam leo molestie sed luctus quis feugiat in pede Fusce tellus Sed metus augue convall</p>
    <p>consequat nec porta vel lectus Nulla sit amet diam Duis non nunc Nulla rhoncus dictum metus Curabitur tristique mi condimentum orci Phasellus pellentesque aliquam</p>
  </div>
  <a class="btn btn-white" style="left:151px;top:1674px;width:175px;height:50px">Book Now</a>

  <div class="abs calendar">
    <div class="calendar-head"><b>&lsaquo;</b><span>JUNE 2020</span><b>&rsaquo;</b></div>
    <table>
      <tr><th>MO</th><th>TU</th><th>WE</th><th>TH</th><th>FR</th><th>SA</th><th>SU</th></tr>
      <tr><td>1</td><td>2</td><td>3</td><td>4</td><td>5</td><td>6</td><td>7</td></tr>
      <tr><td>8</td><td>9</td><td>10</td><td>11</td><td>12</td><td>13</td><td>14</td></tr>
      <tr><td>15</td><td>16</td><td>17</td><td>18</td><td>19</td><td>20</td><td>21</td></tr>
      <tr><td>22</td><td>23</td><td>24</td><td>25</td><td>26</td><td>27</td><td>28</td></tr>
      <tr><td></td><td>30</td><td>31</td><td></td><td></td><td></td><td></td></tr>
    </table>
  </div>
</section>

<section class="how-it-works">
  <h2 class="abs heading section-title" style="top:1918px">How It Works</h2>
  <svg class="abs steps" viewBox="0 0 1200 200" aria-hidden="true">
    <g fill="none" stroke="var(--blue)" stroke-width="2.5">
      <line x1="345" y1="67" x2="485" y2="67" stroke-dasharray="2 4" stroke-width="1.5"/>
      <line x1="657" y1="67" x2="815" y2="67" stroke-dasharray="2 4" stroke-width="1.5"/>
      <circle cx="283" cy="67" r="61"/>
      <circle cx="590" cy="67" r="61"/>
      <circle cx="915" cy="67" r="61"/>
      <!-- bicycle icon -->
      <circle cx="268" cy="78" r="13"/><circle cx="308" cy="78" r="13"/>
      <path d="M268 78 L282 56 L302 56 L308 78 M282 56 L290 78 L302 56 M278 50 H288"/>
      <!-- calendar icon -->
      <rect x="562" y="45" width="52" height="46" rx="4"/>
      <line x1="562" y1="58" x2="614" y2="58"/>
      <line x1="574" y1="39" x2="574" y2="50"/><line x1="602" y1="39" x2="602" y2="50"/>
      <circle cx="608" cy="86" r="10" fill="var(--paper)"/>
      <path d="M603 86 L607 90 L613 82"/>
      <!-- card icon -->
      <rect x="888" y="45" width="62" height="42" rx="4"/>
      <line x1="888" y1="56" x2="950" y2="56" stroke-width="5"/>
      <line x1="896" y1="72" x2="920" y2="72"/><line x1="896" y1="79" x2="914" y2="79"/>
    </g>
    <g font-family="Titillium Web, Arial, sans-serif" font-size="92" font-weight="400" fill="var(--paper)" stroke="var(--blue)" stroke-width="2.5">
      <text x="185" y="103">1</text>
      <text x="490" y="103">2</text>
      <text x="812" y="103">3</text>
    </g>
  </svg>
  <div class="step-label" style="left:173px;top:2150px">Choose Your<br>Bicycle</div>
  <div class="step-label" style="left:484px;top:2150px">Select Your<br>Date &amp; Time</div>
  <div class="step-label" style="left:818px;top:2150px">Pay &amp; Enjoy<br>Your Journey</div>

  <div class="abs people-photo" role="img" aria-label="Two riders on fat tire bicycles on a grassy hillside under a cloudy sky" style="top:2200px;height:380px"></div>
  <svg class="abs people-edge" viewBox="0 0 1200 95" preserveAspectRatio="none" aria-hidden="true">
    <path d="M0 85 Q200 30 380 60 T700 40 T1000 55 T1200 45 V95 H0 Z" fill="var(--paper)"/>
  </svg>
</section>

<section class="testimonials">
  <h2 class="abs heading section-title" style="top:2588px">What People Says</h2>
  <div class="abs testimonial-img" style="left:118px;background:linear-gradient(180deg,#b7cde0,#6f8fa8 60%,#4a5f70)" role="img" aria-label="Cyclist with a backpack riding along a beach"></div>
  <div class="abs testimonial-img" style="left:451px;background:linear-gradient(180deg,#5f8fc4,#a6c2dd 60%,#6c7a84)" role="img" aria-label="Rider in a red jacket on a fat tire bicycle at the shore"></div>
  <div class="abs testimonial-img" style="left:785px;background:linear-gradient(180deg,#c9d8e6,#7d93a6 55%,#5c4d3f)" role="img" aria-label="Rider resting beside a fat tire bicycle on rocks by a lake"></div>
  <div class="testimonial-card" style="left:137px">Lorem ipsum dolor sit amet consectetuer adipiscing elit Nam cursus Morbi ut mi Nullam enim leo egestas id condimentum<strong>By Author Name</strong></div>
  <div class="testimonial-card featured" style="left:469px">Lorem ipsum dolor sit amet consectetuer adipiscing elit Nam cursus Morbi ut mi Nullam enim leo egestas id condimentum<strong>By Author Name</strong></div>
  <div class="testimonial-card" style="left:803px">Lorem ipsum dolor sit amet consectetuer adipiscing elit Nam cursus Morbi ut mi Nullam enim leo egestas id condimentum<strong>By Author Name</strong></div>
</section>

<section class="cta">
  <div class="abs cta-photo" role="img" aria-label="Rider in a helmet riding a mountain bicycle over rocks above a lake"></div>
  <h2 class="abs heading cta-title">Start Your Journey<br>with Tall Fern</h2>
  <p class="abs cta-text">Aonsequat nec porta vel lectus Nulla sit amet diam Duis non nunc Nulla rhoncus dictum metus Curabitur tristique mi condimentum orci Phasellus pellentesque aliquam</p>
  <a class="btn btn-white" style="left:146px;top:3419px;width:184px;height:55px">Book Now</a>
  <svg class="abs footer-edge" viewBox="0 0 1200 70" preserveAspectRatio="none" aria-hidden="true">
    <path d="M0 60 Q120 10 260 40 T560 25 T860 45 T1200 20 V70 H0 Z" fill="var(--footer)"/>
  </svg>
</section>

<footer>
  <div class="abs site-footer"></div>
  <div class="abs footer-mark">Tall<br>Fern</div>
  <div class="abs footer-col" style="left:365px">
    <h4>Quick Links</h4>
    <ul><li class="indent">Home</li><li class="indent">About</li><li class="indent">Rent bicycles</li><li class="indent">Testimonials</li></ul>
  </div>
  <div class="abs footer-col" style="left:544px">
    <h4>Resources</h4>
    <ul><li class="indent">Blogs</li><li class="indent">Book Now</li><li class="indent">Calendar</li><li class="indent">Contact Us</li></ul>
  </div>
  <div class="abs footer-col" style="left:709px">
    <h4>Contact Us</h4>
    <ul><li>48 Ridgeway Lane</li><li>Fernvale 20417</li><li>555.014.2280</li><li>hello@tallfernrental.com</li></ul>
  </div>
  <div class="abs footer-col" style="left:923px">
    <h4>Follow Us</h4>
    <div class="social"><i></i><i></i><i></i><i></i></div>
  </div>
  <div class="abs footer-bar">&copy; 2020 Company Name &nbsp;All right reserved</div>
</footer>

</body>
</html>
```